Stationery for Villa Marenta Design Hotel**

Who we are:

Wander on an isolated beach while breathing in the fresh, salty, sea air. Listen to the warm Pacific wind rustling through green palm trees as you walk to a pristine lagoon. Feel the delicious warmth of the sun kiss your skin; the beach is yours. At Villa Marenta you can experience a vacation in undisturbed, natural beauty. We have created a place for you to find new strength, relaxation, and inner harmony. We offer total rest to the experienced traveler from all over the world.

We are a brand new and smartly built design-hotel (under construction) close to a unique beach and a fantastic surf spot in Huatulco, Southwest Mexico.

As you can see in the attachments, we do have an established corporate design, but as for now still need a format for booklets for information around our hotel and things to do in the area, important numbers (we fill in the content for that one).

Our corporate colors:
green #64b445, brown #b07043, blue #0ab7cf, yellow # f9b02a and #fcc01a, navy #444f69
Corporate fonts:
Krub and Miller Banner.
For further information access:
www.villamarenta.example
https://slidevault.example/view/QmPxLwZrTyKsNbVcHdJe/

Social Media: VillaMarenta

Industry/Entity Type

Hotel

Font styles to use
Other font styles liked:
• Krub, Miller Banner

Requirements
Must have
• Stick to Logo Design, defined corporate elements, logo, colors, fonts and general touch and feel
Nice to have
• Who we are:

Our corporate colors:
Corporate fonts:
Krub and Miller Banner.
www.villamarenta.example

Social Media: VillaMarenta

```html
<!DOCTYPE html>
<html lang="en">
<head>
<meta charset="utf-8">
<title>Villa Marenta – Registry Card</title>
<link href="https://fonts.googleapis.com/css2?family=Gelasio:wght@400;500&display=swap" rel="stylesheet">
<style>
  :root{
    --page:#ececec;
    --card:#ffffff;
    --ink:#1f1f1f;
    --muted:#6d6d6d;
    --gold:#e0a526;
    --icon:#f0a53a;
    --teal-top:#3cc3cc;
    --teal-bottom:#0d8592;
    --shadow:rgba(0,0,0,.35);
  }
  *{box-sizing:border-box;margin:0;padding:0}
  html,body{width:960px;height:1200px;overflow:hidden;background:var(--page)}
  body{position:relative;font-family:"Gelasio",Georgia,serif;color:var(--ink)}
  .card{position:absolute;left:86px;top:76px;width:792px;height:1048px;background:var(--card);
        box-shadow:4px 4px 3px var(--shadow);border:1px solid #d6d6d6}
  .brand{position:absolute;left:48px;top:37px;width:146px;height:170px}
  .brand-mark{width:40px;height:40px;background:var(--gold)}
  .brand-name{margin-top:14px;font-size:22px;line-height:1.1;color:var(--gold);letter-spacing:.5px}
  .contact{position:absolute;left:222px;top:52px;list-style:none;font-size:19px;color:var(--muted);line-height:1}
  .contact li{position:relative;padding-left:26px;height:32px}
  .contact li.tall{height:63px}
  .contact svg{position:absolute;left:0;top:2px;width:15px;height:15px}
  .contact .line2{display:block;margin-top:12px}
  .serial{position:absolute;left:527px;top:124px;font-size:32px}
  .title{position:absolute;left:208px;top:254px;width:371px;height:55px;border-radius:12px;
         background:linear-gradient(var(--teal-top),var(--teal-bottom));color:#fff;
         font-size:47px;line-height:55px;text-align:center;letter-spacing:.3px}
  .fields{position:absolute;left:48px;top:320px;width:722px;list-style:none;font-size:34px}
  .field{display:flex;height:45.4px;align-items:baseline;white-space:nowrap;overflow:hidden}
  .field.spacer{height:50px}
  .leader{flex:1;overflow:hidden;margin-left:8px;letter-spacing:1px}
  .leader::after{content:"........................................................................................................................"}
  .signature{position:absolute;left:48px;top:960px;font-size:34px}
</style>
</head>
<body>
  <main class="card">
    <div class="brand">
      <div class="brand-mark"></div>
      <div class="brand-name">VILLA MARENTA</div>
    </div>

    <ul class="contact">
      <li class="tall">
        <svg viewBox="0 0 16 16"><rect width="16" height="16" rx="2" fill="var(--icon)"/><path d="M8 3a3.5 3.5 0 0 0-3.5 3.5C4.5 9 8 13 8 13s3.5-4 3.5-6.5A3.5 3.5 0 0 0 8 3zm0 4.8a1.3 1.3 0 1 1 0-2.6 1.3 1.3 0 0 1 0 2.6z" fill="#fff"/></svg>
        Villa Marenta, Playa Serena,<span class="line2">Huatulco, Oaxaca, Mexiko</span>
      </li>
      <li>
        <svg viewBox="0 0 16 16"><rect width="16" height="16" rx="2" fill="var(--icon)"/><path d="M5 3.5l2 2.2-1 1.2c.7 1.4 1.7 2.4 3.1 3.1l1.2-1 2.2 2-1.2 1.5C8 12.3 3.7 8 3.5 4.7z" fill="#fff"/></svg>
        +52 1 (958) 555 0142
      </li>
      <li>
        <svg viewBox="0 0 16 16"><rect x="1" y="3" width="14" height="10" fill="none" stroke="var(--icon)" stroke-width="1.5"/><path d="M1.5 3.5L8 9l6.5-5.5" fill="none" stroke="var(--icon)" stroke-width="1.5"/></svg>
        hello@villamarenta.example
      </li>
      <li>
        <svg viewBox="0 0 16 16"><circle cx="8" cy="8" r="6.5" fill="none" stroke="var(--icon)" stroke-width="1.5"/><path d="M1.5 8h13M8 1.5c-3 3.5-3 9.5 0 13M8 1.5c3 3.5 3 9.5 0 13" fill="none" stroke="var(--icon)" stroke-width="1.2"/></svg>
        www.villamarenta.example
      </li>
    </ul>

    <div class="serial">No.</div>

    <h1 class="title" style="font-weight:400">Registry Card</h1>

    <ul class="fields">
      <li class="field">Arival Date<span class="leader"></span></li>
      <li class="field">Departure Date<span class="leader" style="margin-left:0"></span></li>
      <li class="field">Room<span class="leader"></span></li>
      <li class="field">No. Guest (s)<span class="leader"></span></li>
      <li class="field spacer"><span class="leader" style="margin-left:0"></span></li>
      <li class="field">Name<span class="leader"></span></li>
      <li class="field">Last Name<span class="leader"></span></li>
      <li class="field">Date of birth<span class="leader"></span></li>
      <li class="field">City-State-Zip code<span class="leader"></span></li>
      <li class="field">Country<span class="leader"></span></li>
      <li class="field">Email<span class="leader"></span></li>
      <li class="field">Telephone<span class="leader"></span></li>
      <li class="field">Comments<span class="leader"></span></li>
    </ul>

    <div class="signature">Signature</div>
  </main>
</body>
</html>
```